Looking for a cool, modern Cannabis Jar Label

I want you to come up with a better, modern look for a label.

I need it sized to 4” x 3” - I plan to print directly to label printer.

I want you to use Photoshop and deliver me a layered PSD file that I can edit and modify the information as needed..

The label information will need to include places for:
(1) Strain Name - most important part of label - larger font size than rest - example Kestrel Mist, PLV #7, Juniper Hollow
(2) Pricing - for Gram, 1/8, 1/4, 1/2. and Ounce
(3) Strain Designation (Hybrid, Indica or Sativa) - maybe color coded, different color for Indica v. Sativa, just an idea
(4) THC and CBD percentages - for example 23% THC and 0.05% CBD
(5) Farm name - a place where we can add the name/logo of the business that produced the product. example - Ovenrow Farms

I have attached a simple mockup showing the information.

I have also attached a few samples of labels we like to give you an idea of the look and feel we are going for.

I am wanting a very clean, modern, classy, readable look.The font will use is Gotham Font.

HI Everyone! Thank you for all of your designs. I am requesting an extension because I need more time to give adequate feedback to the designers. Thank you for your participation and all of your efforts! I will be making a decision soon!

• Gotham Font

• Thank you for your designs. I am sorry i have been slow in providing feedback, things have been really busy around here!
• I wanted to give some group general feedback. After reviewing all of the designs, there is a common theme among all of the designs that I would like to see changed.
• I would like to see the per gram pricing more prominent on the label. This is what most people are looking for when they are purchasing the product. So I would like to see this stand out from the other pricing tiers. As I think about it, they don't all need to be grouped together in a line. You could have the Per Gram pricing front and center some where and then the other pricing tiers grouped together somewhere else on the label.
• This is the order of importance of items on the label. Items at the the top of the list should be bigger than those below it.
• 1. Strain name
• 2. Pricing - being per gram the most important of all prices
• 3. THC/CBD percentages
• 4. Strain Type (indica, sativa, hybrid)
• 5. Farm name/logo
• When laying out these labels, they will be going on rounded jars and they will be on display. Think of jars with fancy labels in a candy store. They need to be eye catchy, appealing, but easy read.
• Thank you for all of your hard work, everyone is doing a great job.
• Best,
• Neta

```html
<!DOCTYPE html>
<html lang="en">
<head>
<meta charset="utf-8">
<title>Kestrel Mist Jar Label</title>
<link rel="stylesheet" href="https://fonts.googleapis.com/css2?family=Montserrat:wght@300;400;500;700;800&display=swap">
<style>
  :root {
    --maroon: #820404;
    --rose-panel: #c68787;
    --blush-line: #ddb9b9;
    --band-mid: #9c3636;
    --band-value: #a84c4c;
    --band-pale: #dbb3b3;
    --grown-band: #cd5555;
    --ink: #111111;
    --white: #ffffff;
  }
  html, body {
    margin: 0;
    padding: 0;
    width: 1200px;
    height: 917px;
    overflow: hidden;
    background: var(--white);
  }
  .label {
    position: absolute;
    left: 0;
    top: 0;
    width: 1280px;
    height: 978px;
    transform: scale(0.9375);
    transform-origin: 0 0;
    font-family: "Montserrat", sans-serif;
  }
  .label-frame {
    position: absolute;
    left: 35px;
    top: 35px;
    width: 1202px;
    height: 902px;
    background: var(--maroon);
  }
  .strain-name {
    position: absolute;
    left: 78px;
    top: 52px;
    margin: 0;
    color: var(--white);
    font-weight: 400;
    line-height: 1;
    text-shadow: 2px 3px 4px rgba(0,0,0,0.35);
  }
  .strain-name .primary {
    display: block;
    font-size: 114px;
    letter-spacing: 1px;
  }
  .strain-name .secondary {
    display: block;
    font-size: 90px;
    margin-top: 14px;
    margin-left: 4px;
  }
  .strain-type {
    position: absolute;
    left: 1067px;
    top: 42px;
    width: 161px;
    height: 265px;
    background: var(--rose-panel);
  }
  .strain-type span {
    position: absolute;
    left: 50%;
    top: 50%;
    transform: translate(-50%, -50%) rotate(-90deg);
    font-size: 58px;
    font-weight: 300;
    color: var(--ink);
    white-space: nowrap;
  }
  .price-board {
    position: absolute;
    left: 42px;
    top: 310px;
    width: 1186px;
    height: 355px;
    background: var(--white);
  }
  .price-card {
    position: absolute;
    top: 23px;
    height: 315px;
    box-sizing: border-box;
    border-right: 4px solid var(--blush-line);
    border-bottom: 4px solid var(--blush-line);
  }
  .price-card .amount {
    position: absolute;
    left: 0;
    right: 0;
    top: 28px;
    text-align: center;
    font-size: 90px;
    font-weight: 300;
    color: var(--ink);
    line-height: 1;
    letter-spacing: -1px;
  }
  .price-card .unit {
    position: absolute;
    left: 50%;
    top: 150px;
    width: 130px;
    height: 130px;
    margin-left: -65px;
    border-radius: 50%;
    background: var(--maroon);
    color: var(--white);
    font-size: 58px;
    font-weight: 300;
    line-height: 130px;
    text-align: center;
  }
  .potency {
    position: absolute;
    left: 42px;
    top: 675px;
    width: 816px;
    height: 253px;
  }
  .potency svg {
    position: absolute;
    left: 0;
    top: 0;
  }
  .potency .heading {
    position: absolute;
    top: 30px;
    font-size: 62px;
    font-weight: 800;
    color: var(--white);
    line-height: 1;
    text-shadow: 2px 3px 4px rgba(0,0,0,0.35);
  }
  .potency .value {
    position: absolute;
    top: 138px;
    font-size: 100px;
    font-weight: 400;
    line-height: 1;
  }
  .potency .value sup {
    font-size: 44px;
    vertical-align: top;
    position: relative;
    top: 4px;
  }
  .thc-value { color: var(--white); text-shadow: 2px 3px 4px rgba(0,0,0,0.35); }
  .cbd-value { color: var(--ink); }
  .grower {
    position: absolute;
    left: 865px;
    top: 675px;
    width: 363px;
    height: 253px;
  }
  .grower-band {
    height: 60px;
    background: var(--grown-band);
    color: var(--ink);
    font-size: 44px;
    font-weight: 300;
    line-height: 60px;
    text-align: center;
    letter-spacing: 1px;
  }
  .grower-name {
    position: absolute;
    left: 0;
    top: 62px;
    width: 363px;
    height: 191px;
    background: var(--white);
    display: flex;
    align-items: center;
    justify-content: center;
    gap: 16px;
  }
  .grower-mark {
    width: 70px;
    height: 70px;
    border-radius: 50%;
    background: var(--ink);
    flex: none;
  }
  .grower-text {
    font-size: 38px;
    font-weight: 700;
    color: var(--ink);
    line-height: 1.05;
  }
</style>
</head>
<body>
<div class="label">
  <div class="label-frame"></div>

  <h1 class="strain-name">
    <span class="primary">Kestrel Mist</span>
    <span class="secondary">Juniper Hollow</span>
  </h1>

  <div class="strain-type"><span>Hybrid</span></div>

  <div class="price-board">
    <div class="price-card" style="left:18px;width:175px;">
      <div class="amount">$10</div>
      <div class="unit">g.</div>
    </div>
    <div class="price-card" style="left:216px;width:189px;">
      <div class="amount">$35</div>
      <div class="unit">1/8</div>
    </div>
    <div class="price-card" style="left:430px;width:193px;">
      <div class="amount">$70</div>
      <div class="unit">1/4</div>
    </div>
    <div class="price-card" style="left:648px;width:234px;">
      <div class="amount">$140</div>
      <div class="unit">1/2</div>
    </div>
    <div class="price-card" style="left:906px;width:261px;">
      <div class="amount">$280</div>
      <div class="unit">Oz</div>
    </div>
  </div>

  <div class="potency">
    <svg width="816" height="253" viewBox="0 0 816 253" aria-hidden="true">
      <rect x="0" y="0" width="816" height="125" fill="var(--band-mid)"/>
      <polygon points="0,0 318,0 387,125 0,125" fill="var(--maroon)"/>
      <rect x="0" y="125" width="816" height="128" fill="var(--band-pale)"/>
      <polygon points="0,125 387,125 458,253 0,253" fill="var(--band-value)"/>
    </svg>
    <div class="heading" style="left:84px;">THC</div>
    <div class="heading" style="left:512px;">CBD</div>
    <div class="value thc-value" style="left:80px;">28<sup>%</sup></div>
    <div class="value cbd-value" style="left:460px;">0.05<sup>%</sup></div>
  </div>

  <div class="grower">
    <div class="grower-band">Grown by</div>
    <div class="grower-name">
      <div class="grower-mark"></div>
      <div class="grower-text">Ovenrow<br>Farms</div>
    </div>
  </div>
</div>
</body>
</html>
```